Front and content page design for Fitness Cookbook

I am looking for someone to Design a front cover for a Recipe book and also create an amazing layout for the book.

Its for a corporate seminar so has to be eye catching, professional and bold.

Content is complete

Target Market(s)

Industry/Entity Type

Health And Wellness

Font styles to use
Sans Serif

Requirements
Must have
• Eye catching, professional and bold.
• By Dorian as stated on the document
• Must have Tidewell Motion Logo on it.

```html
<!DOCTYPE html>
<html lang="en">
<head>
<meta charset="utf-8">
<title>Protein Porridge – Recipe Page</title>
<link rel="stylesheet" href="https://fonts.googleapis.com/css2?family=Lato:wght@400;700&display=swap">
<style>
  :root {
    --page: #ffffff;
    --accent: #f29a1f;
    --ink: #3a3a3a;
    --white: #ffffff;
    --photo-light: #d8c8b8;
    --photo-dark: #9a7c66;
  }
  * { margin: 0; padding: 0; box-sizing: border-box; }
  html, body { width: 849px; height: 1200px; overflow: hidden; background: var(--page); }
  .page {
    position: relative;
    width: 849px; height: 1200px;
    background: var(--page);
    font-family: "Lato", sans-serif;
    color: var(--ink);
  }
  .dish-photo {
    position: absolute; left: 0; top: 0;
    width: 849px; height: 467px;
    background: linear-gradient(160deg, var(--photo-light) 0%, var(--photo-dark) 100%);
  }
  .title-band {
    position: absolute; left: 0; top: 467px;
    width: 849px; height: 192px;
    background: var(--accent);
    display: flex; align-items: center; justify-content: center;
  }
  .recipe-title {
    color: var(--white);
    font-weight: 400;
    font-size: 52px;
    letter-spacing: 0.5px;
  }
  .recipe-body {
    position: absolute; left: 52px; top: 683px; width: 750px;
    font-size: 15px; line-height: 1.38;
  }
  .label {
    color: var(--accent);
    font-weight: 700;
    font-size: 17px;
    text-transform: uppercase;
    letter-spacing: 0.3px;
  }
  .label .value {
    color: var(--ink);
    font-weight: 400;
    font-size: 13px;
    text-transform: none;
  }
  .section-heading { margin-top: 22px; }
  .ingredients { list-style: none; margin-top: 4px; }
  .method { margin-top: 4px; }
  .page-footer {
    position: absolute; left: 52px; top: 1158px;
    display: flex; align-items: center; gap: 10px;
    font-size: 13px;
  }
  .brand { display: flex; align-items: center; gap: 5px; color: var(--ink); font-size: 11px; font-weight: 700; }
  .brand-dot { width: 10px; height: 10px; border-radius: 50%; background: var(--accent); }
</style>
</head>
<body>
<main class="page">
  <div class="dish-photo" role="img" aria-label="Photo of chocolate protein porridge in a white bowl with a spoon"></div>

  <header class="title-band">
    <h1 class="recipe-title">Protein Porridge</h1>
  </header>

  <section class="recipe-body">
    <p class="label">Prep time <span class="value">2 mins</span></p>
    <p class="label">Cooking time <span class="value">3 mins</span></p>

    <h2 class="label section-heading">Ingredients</h2>
    <ul class="ingredients">
      <li>100g organic porridge oats</li>
      <li>1 tablespoon 100% natural nut butter</li>
      <li>1 cup water</li>
      <li>1 scoop chocolate protein powder Dash of cinnamon</li>
      <li>1 tsp shredded coconut (optional)</li>
    </ul>

    <h2 class="label section-heading">Cooking instructions</h2>
    <p class="method">Add the oats and nut butter into a bowl and cover with water (or so all the oats are covered). Microwave on full power for 2-3 minutes until majority of the water has been used up. Add the protein powder and mix well. Sprinkle the cinnamon and shredded coconut on top.</p>
  </section>

  <footer class="page-footer">
    <span class="page-number">18</span>
    <span class="brand"><span class="brand-dot"></span>Tidewell Motion</span>
  </footer>
</main>
</body>
</html>
```